Tandem Hearth Works Pty Ltd

We need business cards for a company based in Perth, we install, service and maintain fire equipment.
On the front we want a great design with our logo and a small spot for our full company name, general company email address and office number. On the back we need space for our name, title, mobile number and email address on the back.

Target Market(s)

Facility managers and commercial/industrial building owners/occupiers.

Contact Information for Business Card

Font styles to use
Sans Serif

Requirements
Must have
• Please only submit 5 of your best samples.
Darker tones are preferred.
Nice to have
• We want to use, black, red and grey. Keep it modern and clean.
I've attached the company logo and a sample of a boarder we use on our emergency plans.
Should not have
• No preference. Let the designer choose.

```html
<!DOCTYPE html>
<html lang="en">
<head>
<meta charset="utf-8">
<title>Tandem Hearth Works Pty Ltd — Business Cards</title>
<link rel="stylesheet" href="https://fonts.googleapis.com/css2?family=Arimo:wght@400;700&display=swap">
<style>
  :root {
    --page: #1c1c1c;
    --card: #111111;
    --red: #ff1010;
    --brand-red: #e5212f;
    --grey: #808080;
    --text-light: #d6d6d6;
    --divider: #4a4a4a;
  }
  * { box-sizing: border-box; margin: 0; padding: 0; }
  html, body {
    width: 1200px; height: 1015px; overflow: hidden;
    background: radial-gradient(ellipse at center, #2a2a2a 0%, var(--page) 60%, #0c0c0c 100%);
    font-family: "Arimo", Arial, sans-serif;
  }
  .card {
    position: absolute;
    width: 760px; height: 434px;
    background: var(--card);
    overflow: hidden;
    box-shadow: 0 18px 40px rgba(0,0,0,.6);
  }
  .card--front { left: 110px; top: 48px; }
  .card--back  { left: 330px; top: 532px; }
  .card__band { position: absolute; left: 0; top: 0; width: 760px; height: 434px; }
  .wordmark {
    position: absolute; left: 70px; top: 165px; width: 250px;
    color: var(--brand-red); font-weight: 700; font-size: 40px;
    line-height: 1.05; letter-spacing: 1px;
  }
  .divider {
    position: absolute; left: 345px; top: 120px;
    width: 1px; height: 150px; background: var(--divider);
  }
  .details { position: absolute; left: 380px; top: 118px; width: 360px; }
  .company-name {
    color: var(--brand-red); font-weight: 700; font-size: 22px;
    line-height: 1.1; text-transform: uppercase;
  }
  .office-phone {
    color: var(--text-light); font-weight: 700; font-size: 28px;
    margin: 12px 0 10px;
  }
  .person-name {
    color: var(--brand-red); font-weight: 700; font-size: 24px;
    text-transform: uppercase;
  }
  .person-title { color: var(--text-light); font-size: 17px; margin: 4px 0 24px; }
  .contact-row {
    display: flex; align-items: center; gap: 10px;
    color: var(--text-light); font-size: 17px; margin-bottom: 6px;
  }
  .contact-row svg { width: 18px; height: 18px; flex: none; }
</style>
</head>
<body>

<svg width="0" height="0" style="position:absolute">
  <defs>
    <clipPath id="band-shape">
      <polygon points="0,408 760,318 760,434 0,434"/>
    </clipPath>
    <g id="stripe-band">
      <g clip-path="url(#band-shape)">
        <rect x="0" y="300" width="760" height="134" fill="#808080"/>
        <polygon points="0,300 200,300 110,434 0,434" fill="#ff1010"/>
        <polygon points="330,300 560,300 470,434 240,434" fill="#ff1010"/>
        <polygon points="660,300 760,300 760,434 570,434" fill="#ff1010"/>
      </g>
      <line x1="0" y1="420" x2="760" y2="330" stroke="#ff1010" stroke-width="3"/>
    </g>
  </defs>
</svg>

<section class="card card--front" aria-label="Front of business card">
  <svg class="card__band" viewBox="0 0 760 434" aria-hidden="true"><use href="#stripe-band"/></svg>
  <div class="wordmark">TANDEM<br>HEARTH</div>
  <div class="divider"></div>
  <div class="details">
    <p class="company-name">Tandem Hearth<br>Works Pty Ltd</p>
    <p class="office-phone">555.0142.0190</p>
    <p class="contact-row">
      <svg viewBox="0 0 18 18"><rect x="1" y="4" width="16" height="11" fill="var(--brand-red)"/><polyline points="1,4 9,11 17,4" fill="none" stroke="var(--card)" stroke-width="1.5"/></svg>
      info@tandemhearth.com
    </p>
    <p class="contact-row">
      <svg viewBox="0 0 18 18" fill="none" stroke="var(--brand-red)" stroke-width="1.5"><circle cx="9" cy="9" r="7.5"/><ellipse cx="9" cy="9" rx="3.5" ry="7.5"/><line x1="1.5" y1="9" x2="16.5" y2="9"/></svg>
      www.tandemhearth.com
    </p>
  </div>
</section>

<section class="card card--back" aria-label="Back of business card">
  <svg class="card__band" viewBox="0 0 760 434" aria-hidden="true"><use href="#stripe-band"/></svg>
  <div class="wordmark">TANDEM<br>HEARTH</div>
  <div class="divider"></div>
  <div class="details">
    <p class="person-name">Marcus Ellery</p>
    <p class="person-title">Managing Director</p>
    <p class="contact-row">
      <svg viewBox="0 0 18 18" fill="none" stroke="var(--brand-red)" stroke-width="1.8"><rect x="4" y="1.5" width="10" height="15" rx="1.5"/><line x1="7.5" y1="13.5" x2="10.5" y2="13.5"/></svg>
      555.0163.0177
    </p>
    <p class="contact-row">
      <svg viewBox="0 0 18 18"><rect x="1" y="4" width="16" height="11" fill="var(--brand-red)"/><polyline points="1,4 9,11 17,4" fill="none" stroke="var(--card)" stroke-width="1.5"/></svg>
      marcus@tandemhearth.com
    </p>
  </div>
</section>

</body>
</html>
```